International Film making Business needs the 5 Logos provided made into a POSTER Format

Design Task:
CREATE A POSTER DESIGN USING THE 5 LOGOS PROVIDED. The BOLD BRIGHT HORIZON LOGO should stand out from the others by being in the middle with the other 4 logos connected to it somehow.

The 5 Businesses already has their 5 Logos, all similar in design to each other.

BOLD BRIGHT HORIZON is the Main Logo that encompasses the other 4 Logos. So it must stand out more and it is like the Overall Business entity that incorporates the other 4 Logos.

What is required is that by using the 5 Logo designs provided, create a cool graphic artwork that somehow incorporates ALL of the 5 Logos - But having the BOLD BRIGHT HORIZON Logo at the forefront/most important/standing out the most.
- BOLD BRIGHT HORIZON will probably be bigger than the others
- and could be changed into 3D.

I have attached all 5 logos and a hand drawn example of how the BOLD BRIGHT HORIZONS could stand out from the rest.

THE DESIGNS OF THE LOGOS SHOULD NOT BE CHANGED (except the BOLDBRIGHTHORIZON which can be 3D)

Please do not be restricted with the sample idea. Creativity is encouraged

DIMENSION: 3000 mm x 6000 mm
high resolution graphic

Logo Text

bold bright , bold bright pictures, bold bright legends, bold bright groovy, BOLD BRIGHT HORIZONS

Requirements
Must have
• USE THE 5 LOGOS PROVIDED ONLY - Only BOLD BRIGHT HORIZON can be changed into 3D only
Nice to have
• Eye catching design, showing the Bold Bright Horizon as the most powerful Logo that has the other 4 as subordinate companies
Should not have
• ANY CHANGE IN THE 5 LOGO DESIGNS (EXcept 3D for Bold Bright Horizons)

```html
<!DOCTYPE html>
<html lang="en">
<head>
<meta charset="utf-8">
<title>Bold Bright Horizons – Group Poster</title>
<link rel="stylesheet" href="https://fonts.googleapis.com/css2?family=Cinzel:wght@600;700&family=Raleway:wght@300&display=swap">
<style>
  :root {
    --bg-edge: #c3c3c3;
    --bg-mid: #fbfbfb;
    --pole-dark: #7d7d7d;
    --pole-light: #c9c9c9;
    --blue: #1f7fc8;
    --blue-deep: #1d4e9a;
    --gold: #b8892c;
    --gold-light: #e6c97a;
    --graphite: #1e1e1e;
    --silver: #8a8a8a;
    --green: #2f9a1c;
    --green-deep: #176b12;
    --legend-ink: #6a2a8a;
    --web-ink: #6b6b6b;
  }
  html, body {
    margin: 0;
    width: 682px;
    height: 1200px;
    overflow: hidden;
  }
  body {
    background: linear-gradient(to bottom, var(--bg-edge) 0%, var(--bg-mid) 55%, var(--bg-edge) 100%);
  }
  .poster {
    display: block;
    width: 682px;
    height: 1200px;
  }
  .brand-name {
    font-family: "Cinzel", serif;
    font-weight: 700;
    text-anchor: middle;
  }
  .brand-blue { fill: var(--blue); }
  .brand-legend { fill: var(--legend-ink); }
  .brand-pictures { fill: var(--graphite); }
  .brand-groovy { fill: var(--green); }
  .brand-main { fill: var(--gold); }
  .web-address {
    font-family: "Raleway", sans-serif;
    font-weight: 300;
    fill: var(--web-ink);
    text-anchor: middle;
  }
  .hex-frame {
    fill: none;
    stroke-width: 7;
    stroke-linejoin: round;
  }
  .mark-spot { opacity: 0.85; }
</style>
</head>
<body>
<svg class="poster" viewBox="0 0 1142 2298" preserveAspectRatio="xMidYMid meet" xmlns="http://www.w3.org/2000/svg">
  <defs>
    <linearGradient id="pole-shade" x1="0" x2="1" y1="0" y2="0">
      <stop offset="0" stop-color="var(--pole-dark)"/>
      <stop offset="0.45" stop-color="var(--pole-light)"/>
      <stop offset="1" stop-color="var(--pole-dark)"/>
    </linearGradient>
    <linearGradient id="stroke-blue" x1="0" y1="0" x2="0" y2="1">
      <stop offset="0" stop-color="var(--blue-deep)"/>
      <stop offset="0.5" stop-color="#22a6e0"/>
      <stop offset="1" stop-color="var(--blue-deep)"/>
    </linearGradient>
    <linearGradient id="stroke-rainbow" x1="0" y1="0" x2="0" y2="1">
      <stop offset="0" stop-color="#ff1a1a"/>
      <stop offset="0.2" stop-color="#ffd400"/>
      <stop offset="0.45" stop-color="#e5e500"/>
      <stop offset="0.65" stop-color="#1d3fc4"/>
      <stop offset="0.85" stop-color="#1c9a8a"/>
      <stop offset="1" stop-color="#39d61a"/>
    </linearGradient>
    <linearGradient id="stroke-graphite" x1="0" y1="0" x2="0" y2="1">
      <stop offset="0" stop-color="var(--graphite)"/>
      <stop offset="0.5" stop-color="#a5a5a5"/>
      <stop offset="1" stop-color="var(--graphite)"/>
    </linearGradient>
    <linearGradient id="stroke-green" x1="0" y1="0" x2="0" y2="1">
      <stop offset="0" stop-color="var(--green-deep)"/>
      <stop offset="0.5" stop-color="#3cc421"/>
      <stop offset="1" stop-color="var(--green-deep)"/>
    </linearGradient>
    <linearGradient id="stroke-gold" x1="0" y1="0" x2="0" y2="1">
      <stop offset="0" stop-color="var(--gold)"/>
      <stop offset="0.5" stop-color="var(--gold-light)"/>
      <stop offset="1" stop-color="var(--gold)"/>
    </linearGradient>
    <radialGradient id="main-fill" cx="0.5" cy="0.5" r="0.6">
      <stop offset="0" stop-color="#ffffff"/>
      <stop offset="1" stop-color="#f0f0f0"/>
    </radialGradient>
  </defs>

  <!-- central spine -->
  <g class="spine">
    <rect x="542" y="228" width="55" height="1995" fill="url(#pole-shade)"/>
    <ellipse cx="569.5" cy="228" rx="27.5" ry="8" fill="#a9a9a9"/>
    <ellipse cx="569.5" cy="2223" rx="27.5" ry="8" fill="url(#pole-shade)"/>
  </g>

  <!-- bold bright -->
  <g class="division division-bold-bright">
    <path class="hex-frame" stroke="url(#stroke-blue)" d="M915,35 L1105,143 L1105,388 L910,498 L735,405 Q675,395 673,455 L668,528 L568,581 L472,518 L475,403 L570,360 L640,393 Q705,400 708,340 L710,153 Z"/>
    <circle class="mark-spot" cx="570" cy="470" r="34" fill="var(--blue)"/>
    <text class="brand-name brand-blue" x="900" y="263" font-size="78" textLength="270" lengthAdjust="spacingAndGlyphs">BOLD</text>
    <text class="brand-name brand-blue" x="900" y="343" font-size="78" textLength="270" lengthAdjust="spacingAndGlyphs">BRIGHT</text>
  </g>

  <!-- bold bright legends -->
  <g class="division division-legends">
    <path class="hex-frame" stroke="url(#stroke-rainbow)" d="M225,291 L432,408 L435,603 Q440,650 505,648 L572,615 L665,668 L668,773 L573,836 L475,781 L467,698 Q455,645 410,668 L232,753 L35,641 L37,398 Z"/>
    <circle class="mark-spot" cx="570" cy="725" r="34" fill="var(--legend-ink)"/>
    <text class="brand-name brand-legend" x="225" y="518" font-size="50" textLength="315" lengthAdjust="spacingAndGlyphs">BOLDBRIGHT</text>
    <text class="brand-name brand-legend" x="225" y="578" font-size="58" textLength="315" lengthAdjust="spacingAndGlyphs">LEGENDS</text>
  </g>

  <!-- bold bright horizons (main) -->
  <g class="division division-main">
    <polygon class="hex-frame" fill="url(#main-fill)" stroke="url(#stroke-gold)" points="575,885 835,1033 835,1343 573,1485 313,1343 313,1033"/>
    <circle class="mark-spot" cx="575" cy="1035" r="78" fill="var(--gold)"/>
    <text class="brand-name brand-main" x="575" y="1218" font-size="74" textLength="450" lengthAdjust="spacingAndGlyphs">BOLD BRIGHT</text>
    <text class="brand-name brand-main" x="575" y="1298" font-size="74" textLength="450" lengthAdjust="spacingAndGlyphs">HORIZONS</text>
    <text class="web-address" x="575" y="1338" font-size="30" textLength="450" lengthAdjust="spacingAndGlyphs">boldbrighthorizons.com.au</text>
  </g>

  <!-- bold bright pictures -->
  <g class="division division-pictures" transform="translate(0,1037)">
    <path class="hex-frame" stroke="url(#stroke-graphite)" d="M225,291 L432,408 L435,603 Q440,650 505,648 L572,615 L665,668 L668,773 L573,836 L475,781 L467,698 Q455,645 410,668 L232,753 L35,641 L37,398 Z"/>
    <circle class="mark-spot" cx="570" cy="725" r="34" fill="var(--silver)"/>
    <text class="brand-name brand-pictures" x="225" y="506" font-size="50" textLength="290" lengthAdjust="spacingAndGlyphs">BOLD BRIGHT</text>
    <text class="brand-name brand-pictures" x="225" y="591" font-size="64" textLength="300" lengthAdjust="spacingAndGlyphs">PICTURES</text>
  </g>

  <!-- bold bright groovy -->
  <g class="division division-groovy" transform="translate(0,1553)">
    <path class="hex-frame" stroke="url(#stroke-green)" d="M915,35 L1105,143 L1105,388 L910,498 L735,405 Q675,395 673,455 L668,528 L568,581 L472,518 L475,403 L570,360 L640,393 Q705,400 708,340 L710,153 Z"/>
    <circle class="mark-spot" cx="570" cy="470" r="34" fill="var(--green)"/>
    <text class="brand-name brand-groovy" x="895" y="265" font-size="50" textLength="300" lengthAdjust="spacingAndGlyphs">BOLD BRIGHT</text>
    <text class="brand-name brand-groovy" x="895" y="340" font-size="64" textLength="300" lengthAdjust="spacingAndGlyphs">GROOVY</text>
  </g>
</svg>
</body>
</html>
```